Redesign of General Contractor Website

I currently have a wordpress site that needs some work. I would like to revitalize what we currently have to look more modern and up-to-date.
I want to be able to easily post pictures from new jobs and have a link to my own blog (not yet online). My current website can be found at www.brovikbuilders.com
the attached pictures are a site I built in Muse. i really like that sort of theme.
PLEASE NOTE: I am not interested in completely remaking the site, simply adding more functionalty and spicing it up a bit. (more animation, interactive elements, layering, etc...)
Target Market(s)
Property owners, Home owners, business owners, property managers, Decision makers purchasing a construction project, specifically Remodels, renovations, or damage restoration, with some or limited knowledge about how to complete one of those projects.
Industry/Entity Type
Contractor
Coding
Coded - Design and coding required
Number of Pages Required
1 page
Requirements
Must have
- Updateable photo bank displaying pictures from recent jobs that we can easily change and update. An embedded youtube pane showing our most recent video via our youtube channel. Animation and/or transition effects. The small circular logos must stay (I would like to see these be used with animation/transitional effects.
- Must be consistent with other marketing material. This can be found on our facebook page or in the power point file attached.
- Must use colors and fonts found at www.brovikbuilders.com
Nice to have
- Stock photos available if needed.
Should not have
- changes in logo design or re wording of text (use lorim ipsum if needed)
- No multiple pages, redesigning fonts

```html
<!DOCTYPE html>
<html lang="en">
<head>
<meta charset="utf-8">
<title>Brovik Builders</title>
<link href="https://fonts.googleapis.com/css2?family=Fira+Sans:ital,wght@0,400;0,600;0,700;0,800;1,400;1,600&family=Open+Sans:ital,wght@0,400;0,600;0,700;1,400&display=swap" rel="stylesheet">
<style>
:root{
  --orange:#f26522;
  --orange-dark:#d9541a;
  --blue:#2a3d8f;
  --blue-deep:#1f2f74;
  --navy:#0e1430;
  --ink:#333;
  --muted:#666;
  --light:#f4f4f4;
  --field:#e9e9e9;
  --white:#fff;
}
*{box-sizing:border-box;margin:0;padding:0}
html,body{width:1200px;height:5325px;overflow:hidden}
body{position:relative;font-family:"Open Sans",Arial,sans-serif;color:var(--ink);background:var(--white)}
.section{position:absolute;left:0;width:1200px}
.title{font-family:"Fira Sans",Arial,sans-serif;font-weight:800;font-size:48px;text-align:center;letter-spacing:.5px;text-transform:uppercase}
.title .accent{color:var(--orange)}
.btn-outline{display:inline-block;border:2px solid var(--white);color:var(--white);font-family:"Fira Sans",sans-serif;font-weight:700;font-size:17px;padding:14px 34px;border-radius:26px;letter-spacing:.5px}
.btn-solid{display:inline-block;background:var(--orange);color:var(--white);font-family:"Fira Sans",sans-serif;font-weight:700;font-size:19px;padding:14px 32px;border-radius:28px}

/* hero */
.hero{top:0;height:700px}
.hero-photo{position:absolute;inset:0;background:linear-gradient(180deg,#3a3632 0%,#57504a 45%,#3b3733 100%)}
.hero-photo::after{content:"";position:absolute;inset:0;background:rgba(10,12,25,.45)}
.nav{position:absolute;top:0;left:0;width:1200px;height:56px;background:rgba(10,12,30,.75);display:flex;align-items:center;padding-left:80px}
.nav-item{font-family:"Fira Sans",sans-serif;font-weight:600;font-size:15px;color:var(--white);margin-right:42px;letter-spacing:.5px}
.nav-item.current{background:var(--orange);padding:18px 18px;margin-left:-18px;margin-right:24px}
.nav-phone{position:absolute;right:70px;top:6px;background:var(--orange);color:var(--white);font-family:"Fira Sans",sans-serif;font-weight:700;font-size:19px;padding:10px 24px;border-radius:0 22px 0 22px;display:flex;align-items:center;gap:10px}
.brand-hero{position:absolute;top:210px;left:0;width:1200px;text-align:center}
.brand-hero .name{font-family:"Fira Sans",sans-serif;font-weight:800;font-size:92px;color:var(--white);letter-spacing:3px;line-height:1}
.brand-hero .mark{display:block;width:34px;height:34px;background:var(--orange);margin:0 auto 18px}

/* about */
.about{top:600px;height:560px;background:var(--orange);clip-path:polygon(0 70px,50% 0,100% 70px,100% 100%,0 100%);color:var(--white);text-align:center}
.about .mark{width:26px;height:26px;border:3px solid var(--white);margin:92px auto 10px}
.about .title{color:var(--white)}
.about p{width:1000px;margin:22px auto 0;font-size:15px;line-height:1.75}
.about .btn-outline{margin-top:34px}

/* team */
.team{top:1160px;height:390px;background:var(--white)}
.team .title{color:var(--blue);margin-top:2px}
.team .title::after{content:"";display:block;width:80px;height:4px;background:var(--orange);margin:10px auto 0}
.member{position:absolute;top:130px;width:480px;display:flex;gap:24px}
.member .photo{width:190px;height:190px;border-radius:50%;flex:none;background:radial-gradient(circle at 50% 40%,#d8b890,#8a6a4c 70%,#5a4636)}
.member h3{font-family:"Fira Sans",sans-serif;font-weight:800;color:var(--orange);font-size:20px;margin-top:14px}
.member .role{font-style:italic;color:var(--blue);font-size:14px;text-decoration:underline;margin:4px 0 12px}
.member p{font-size:14px;line-height:1.6;color:var(--muted)}

/* services */
.services{top:1545px;height:595px;background:var(--blue);color:var(--white);text-align:center}
.services .title{margin-top:52px}
.services .intro{font-style:italic;font-size:15px;line-height:1.6;width:720px;margin:14px auto 0}
.service-row{position:absolute;top:220px;left:110px;width:980px;display:flex;justify-content:space-between}
.service{width:210px}
.service .icon{width:110px;height:110px;border-radius:50%;background:var(--blue-deep);border:3px solid rgba(255,255,255,.25);margin:0 auto;display:flex;align-items:center;justify-content:center}
.service h4{font-family:"Fira Sans",sans-serif;font-weight:800;color:var(--orange);font-size:20px;margin:20px 0 10px}
.service p{font-size:13px;line-height:1.55}
.service p .more{color:var(--orange);font-weight:700}
.arrow-side{position:absolute;top:340px;font-family:"Fira Sans",sans-serif;font-size:40px;color:rgba(255,255,255,.5)}

/* works */
.works{top:2150px;height:460px;background:var(--orange)}
.works .title{color:var(--blue);margin-top:46px}
.works .title .dark{color:var(--blue)}
.works .title .lite{color:var(--white)}
.video{position:absolute;left:75px;top:140px;width:610px;height:300px;background:linear-gradient(135deg,#4a4a4a,#8b8478 55%,#2f2f2f)}
.video-bar{position:absolute;left:0;bottom:0;width:100%;height:34px;background:rgba(0,0,0,.7)}
.video-bar .track{position:absolute;left:12px;right:12px;top:6px;height:3px;background:#888}
.video-bar .track span{display:block;width:8%;height:3px;background:var(--orange)}
.video-play{position:absolute;left:265px;top:105px;width:80px;height:56px;border-radius:14px;background:rgba(0,0,0,.7);display:flex;align-items:center;justify-content:center}
.video-url{position:absolute;left:14px;top:10px;color:var(--white);font-size:14px}
.works-copy{position:absolute;left:720px;top:150px;width:410px;color:var(--white);font-size:14px;line-height:1.65}
.works-copy p{margin-bottom:14px}
.works-copy .btn-outline{margin-top:6px}

/* new job */
.newjob{top:2610px;height:780px;background:var(--white)}
.newjob .title{color:var(--blue);margin-top:50px}
.newjob .title::after{content:"";display:block;width:80px;height:4px;background:var(--orange);margin:10px auto 0}
.banner{position:absolute;left:75px;top:215px;width:1050px;height:290px;background:linear-gradient(90deg,#eceae6 0%,#e0ddd7 45%,#b8a991 70%,#8d7a62 100%)}
.banner .mark{position:absolute;left:36px;top:40px;width:26px;height:26px;border:3px solid var(--blue)}
.banner h3{position:absolute;left:36px;top:80px;font-family:"Fira Sans",sans-serif;font-weight:800;font-size:44px;line-height:1.05;color:var(--blue);text-transform:uppercase}
.banner h3 span{color:var(--orange);display:block}
.banner .tag{position:absolute;left:36px;top:185px;font-style:italic;font-weight:700;color:var(--orange);font-size:15px}
.banner .btn-solid{position:absolute;left:36px;top:216px;display:flex;align-items:center;gap:10px}
.job-strip{position:absolute;left:0;top:515px;width:1200px;height:245px;display:flex;gap:8px}
.job-strip div{flex:1}
.j1{background:linear-gradient(160deg,#a9c3dd,#6e7e8e)}
.j2{background:linear-gradient(160deg,#b88e66,#6a4a30)}
.j3{background:linear-gradient(160deg,#9fb7cf,#8a7764)}
.j4{background:linear-gradient(160deg,#8fb0cf,#b39676)}
.j5{background:linear-gradient(160deg,#c7b08a,#7c5a38)}

/* steps */
.steps{top:3390px;height:510px;background:linear-gradient(180deg,var(--blue) 0%,#33489c 100%);color:var(--white)}
.steps .title{font-size:40px;margin-top:58px;line-height:1.2}
.timeline{position:absolute;left:60px;top:308px;width:1080px;height:3px;background:var(--orange)}
.dot{position:absolute;top:300px;width:18px;height:18px;border-radius:50%;background:var(--orange);border:3px solid var(--white)}
.step{position:absolute;width:220px;text-align:center;font-size:14px;line-height:1.5}
.step b{display:block;color:var(--orange);font-family:"Fira Sans",sans-serif;font-size:15px}
.step.up{top:225px}
.step.down{top:350px}
.stem{position:absolute;width:1px;background:rgba(255,255,255,.55)}

/* badges */
.badges{top:3905px;height:145px;background:var(--orange);display:flex;align-items:center;justify-content:center;gap:26px}
.badge{background:var(--white);opacity:.95}
.badge.rect{width:165px;height:68px}
.badge.round{width:86px;height:86px;border-radius:50%}
.badge.wide{width:190px;height:60px;background:rgba(255,255,255,.85)}

/* contact */
.contact{top:4050px;height:560px;background:var(--white)}
.contact .title{color:var(--blue);margin-top:50px}
.contact .intro{width:720px;margin:18px auto 0;text-align:center;font-style:italic;font-size:15px;line-height:1.6;color:var(--muted)}
.form{position:absolute;left:155px;top:245px;width:890px}
.row{display:flex;gap:16px;margin-bottom:16px}
.field{flex:1;height:46px;background:var(--field);font-size:14px;color:#888;padding:13px 16px}
.field.msg{height:92px}
.submit{display:block;width:175px;margin:24px auto 0;text-align:center}

/* newsletter */
.newsletter{top:4610px;height:410px;background:var(--orange);clip-path:polygon(0 80px,50% 0,100% 80px,100% 100%,0 100%);text-align:center}
.newsletter .title{color:var(--blue);margin-top:120px}
.newsletter p{color:var(--white);font-weight:600;font-size:15px;width:640px;margin:14px auto 0;line-height:1.6}
.sub-row{display:flex;justify-content:center;gap:20px;margin-top:26px}
.sub-row .email{width:480px;height:50px;background:var(--white);text-align:left;padding:14px 20px;font-size:15px;color:#777}
.sub-row .btn-outline{padding:13px 36px}
.socials{display:flex;justify-content:center;gap:14px;margin-top:28px}
.socials span{width:42px;height:42px;border-radius:50%;background:var(--blue);border:2px solid var(--white)}

/* footer */
.footer{top:5020px;height:270px;background:var(--navy);color:var(--white)}
.footer-brand{position:absolute;left:80px;top:70px;font-family:"Fira Sans",sans-serif;font-weight:800;font-size:48px;line-height:1;color:var(--white);letter-spacing:1px}
.footer-brand small{display:block;font-size:48px}
.fcol{position:absolute;top:46px}
.fcol h5{font-family:"Fira Sans",sans-serif;font-weight:700;font-size:17px;color:var(--orange);margin-bottom:16px;letter-spacing:.5px}
.fcol li{list-style:none;font-size:14px;margin-bottom:9px;display:flex;align-items:center;gap:12px}
.fcol li .b{width:8px;height:8px;border-radius:50%;background:var(--orange)}
.follow{display:flex;gap:14px}
.follow span{width:80px;height:60px;background:rgba(255,255,255,.85)}
.copy{top:5290px;height:35px;background:var(--blue-deep);color:var(--white);font-size:13px;text-align:center;line-height:35px}
</style>
</head>
<body>

<header class="section hero">
  <div class="hero-photo" role="img" aria-label="Photograph of a historic stone house at dusk"></div>
  <nav class="nav">
    <span class="nav-item current">HOME</span>
    <span class="nav-item">ABOUT</span>
    <span class="nav-item">SERVICES</span>
    <span class="nav-item">WORK</span>
    <span class="nav-item">CONTACT</span>
    <span class="nav-phone">
      <svg width="20" height="20" viewBox="0 0 24 24"><path fill="#fff" d="M6.6 10.8a15.1 15.1 0 0 0 6.6 6.6l2.2-2.2c.3-.3.7-.4 1-.2 1.1.4 2.3.6 3.6.6.6 0 1 .4 1 1V20c0 .6-.4 1-1 1A17 17 0 0 1 3 4c0-.6.4-1 1-1h3.5c.6 0 1 .4 1 1 0 1.3.2 2.5.6 3.6.1.3 0 .7-.2 1z"/></svg>
      (855) 555-0142
    </span>
  </nav>
  <div class="brand-hero">
    <span class="mark"></span>
    <div class="name">BROVIK<br>BUILDERS</div>
  </div>
</header>

<section class="section about">
  <div class="mark"></div>
  <h2 class="title">About</h2>
  <p>Brovik Builders takes a customer oriented approach to solving all of our clients' needs. Believing that no two projects are ever the same, we pair forward thinking techniques with proven methods to satisfy every customer. While most contracting companies use dated systems, our team stays current with the latest tools and building practices. With our team of certified inspectors, we work hand in hand with our customers to provide unprecedented customer service and the utmost efficiency.</p>
  <p>Based out of Pell County, Brovik Builders does business with the area's insurance companies, real estate agencies, and property managers on a regular basis. Our extensive dealings with these partners have resulted in streamlined response times, and a fast, caring experience for our customers.</p>
  <span class="btn-outline">KNOW MORE</span>
</section>

<section class="section team">
  <h2 class="title">The Team</h2>
  <div class="member" style="left:75px">
    <div class="photo" role="img" aria-label="Portrait of the owner in a hard hat"></div>
    <div>
      <h3>DORN BROVIK</h3>
      <div class="role">Owner</div>
      <p>With a construction background and marketing degree from a state university as his foundation, Dorn started Brovik Builders in 2010. Dorn's vision was to develop the most dependable, customer service</p>
    </div>
  </div>
  <div class="member" style="left:620px">
    <div class="photo" role="img" aria-label="Portrait of the manager"></div>
    <div>
      <h3>ARLO BROVIK</h3>
      <div class="role">Manager</div>
      <p>Arlo oversees internal operations, account management, and web development for Brovik Builders.</p>
    </div>
  </div>
</section>

<section class="section services">
  <h2 class="title">Our <span class="accent">Services</span></h2>
  <p class="intro">Brovik Builders provides professional services for our customers' homes. We work with you to assess your specific needs and guarantee you a custom solution.</p>
  <span class="arrow-side" style="left:30px">&lsaquo;</span>
  <span class="arrow-side" style="right:30px">&rsaquo;</span>
  <div class="service-row">
    <div class="service">
      <div class="icon"><svg width="58" height="44" viewBox="0 0 58 44"><path d="M4 40 29 6l25 34z" fill="#fff"/><path d="M14 40 29 20l15 20" fill="none" stroke="#1f2f74" stroke-width="3"/></svg></div>
      <h4>ROOFING</h4>
      <p>One of the most important parts of your home is the roof. Your roof protects your home from the elements, helps regulate the inside temperature...<span class="more">&raquo;</span></p>
    </div>
    <div class="service">
      <div class="icon"><svg width="50" height="46" viewBox="0 0 50 46"><rect x="2" y="2" width="46" height="42" fill="none" stroke="#fff" stroke-width="3"/><path d="M2 16h46M2 30h46M18 2v14M34 2v14M10 16v14M26 16v14M42 16v14M18 30v14M34 30v14" stroke="#fff" stroke-width="3"/></svg></div>
      <h4>SIDING</h4>
      <p>Old, deteriorating, or damaged siding can leave your house looking incomplete and can pose just as much of a problem as a leaking roof. Over the past few decades...<span class="more">&raquo;</span></p>
    </div>
    <div class="service">
      <div class="icon"><svg width="38" height="50" viewBox="0 0 38 50"><path d="M19 2C19 2 3 22 3 32a16 16 0 0 0 32 0C35 22 19 2 19 2z" fill="#fff"/></svg></div>
      <h4>GUTTERS</h4>
      <p>By diverting water from the base of the building, rain gutters help guard against erosion, leaks, foundation damage, and other serious problems. We build our seamless...<span class="more">&raquo;</span></p>
    </div>
    <div class="service">
      <div class="icon"><svg width="42" height="52" viewBox="0 0 42 52"><rect x="2" y="2" width="38" height="48" fill="none" stroke="#fff" stroke-width="4"/><path d="M21 2v48M2 26h38" stroke="#fff" stroke-width="4"/></svg></div>
      <h4>WINDOWS</h4>
      <p>Rooftops and siding aren't the only parts of your home or business vulnerable to the whims of Mother Nature. Windows, skylights, energy savers, and other...<span class="more">&raquo;</span></p>
    </div>
  </div>
</section>

<section class="section works">
  <h2 class="title"><span class="dark">Our</span> <span class="lite">Works</span></h2>
  <div class="video" role="img" aria-label="Embedded video of a recent roofing job">
    <span class="video-url">www.brovikbuilders.com</span>
    <div class="video-play"><svg width="24" height="26" viewBox="0 0 24 26"><path d="M2 2l20 11L2 24z" fill="#fff"/></svg></div>
    <div class="video-bar"><div class="track"><span></span></div></div>
  </div>
  <div class="works-copy">
    <p>It's easy to tell a client what we can do, but we typically let our portfolio and testimonials speak for themselves. Below you will find the most recent projects we completed for very satisfied home owners. It also helps that we hold an A rating with the Regional Trade Bureau.</p>
    <p>Please take a moment to view our services and if you have any questions please don't hesitate to call or email us using the form below.</p>
    <span class="btn-outline">CONTACT US</span>
  </div>
</section>

<section class="section newjob">
  <h2 class="title">New <span class="accent">Job</span></h2>
  <div class="banner" role="img" aria-label="Painter in a hard hat at work">
    <span class="mark"></span>
    <h3>Our Patinting Services <span>Have You Covered.</span></h3>
    <div class="tag">Superior Results Require The Best Paints Available.</div>
    <span class="btn-solid">
      <svg width="18" height="18" viewBox="0 0 24 24"><path fill="#fff" d="M6.6 10.8a15.1 15.1 0 0 0 6.6 6.6l2.2-2.2c.3-.3.7-.4 1-.2 1.1.4 2.3.6 3.6.6.6 0 1 .4 1 1V20c0 .6-.4 1-1 1A17 17 0 0 1 3 4c0-.6.4-1 1-1h3.5c.6 0 1 .4 1 1 0 1.3.2 2.5.6 3.6.1.3 0 .7-.2 1z"/></svg>
      (855) 555-0142
    </span>
  </div>
  <div class="job-strip">
    <div class="j1" role="img" aria-label="Steel frame of a building under construction"></div>
    <div class="j2" role="img" aria-label="Brick house with new roof"></div>
    <div class="j3" role="img" aria-label="Finished home exterior"></div>
    <div class="j4" role="img" aria-label="Stone house with covered porch"></div>
    <div class="j5" role="img" aria-label="Wooden roof framing"></div>
  </div>
</section>

<section class="section steps" role="region" aria-label="Home repair steps">
  <h2 class="title">A Step-by-Step Guide to Successful<br><span class="accent">Home Repair</span></h2>
  <div class="timeline"></div>
  <span class="dot" style="left:151px"></span>
  <span class="dot" style="left:268px"></span>
  <span class="dot" style="left:389px"></span>
  <span class="dot" style="left:506px"></span>
  <span class="dot" style="left:630px"></span>
  <span class="dot" style="left:754px"></span>
  <span class="dot" style="left:879px"></span>
  <span class="dot" style="left:1013px"></span>
  <div class="step up" style="left:50px"><b>Step 1:</b>Inspection</div>
  <div class="step down" style="left:167px"><b>Step 2:</b>Findings Report and Letter of Intent</div>
  <div class="step up" style="left:288px"><b>Step 3:</b>File an Insurance Claim</div>
  <div class="step down" style="left:405px"><b>Step 4:</b>Schedule a Construction Date &amp; Sign your Contract</div>
  <div class="step up" style="left:529px"><b>Step 5:</b>Initial Payment</div>
  <div class="step down" style="left:653px"><b>Step 6:</b>Construction Day</div>
  <div class="step up" style="left:778px;width:240px"><b>Step 7:</b>Final Invoice and Final Insurance Payment</div>
  <div class="step down" style="left:912px"><b>Step 8:</b>Keep In Touch!</div>
</section>

<section class="section badges" aria-label="Partner and certification badges">
  <span class="badge rect"></span>
  <span class="badge round"></span>
  <span class="badge round"></span>
  <span class="badge wide"></span>
  <span class="badge round"></span>
  <span class="badge round"></span>
  <span class="badge rect"></span>
</section>

<section class="section contact">
  <h2 class="title" style="color:var(--blue)">Contact <span class="accent">Us</span></h2>
  <p class="intro">Thank you for visiting our website. For questions, comments, or suggestions please fill out the form below. To schedule a free inspection call us directly at (855) 555-0142.</p>
  <div class="form">
    <div class="row"><div class="field">Name*</div><div class="field">Last Name*</div><div class="field">Last Name*</div></div>
    <div class="row"><div class="field">Email*</div></div>
    <div class="row"><div class="field msg">Message*</div></div>
    <span class="btn-solid submit">SUBMIT</span>
  </div>
</section>

<section class="section newsletter">
  <h2 class="title">Newsletter</h2>
  <p>Would you like to receive exclusive access to articles, white papers and our regular monthly newsletter?</p>
  <div class="sub-row">
    <div class="email">Enter Your Email</div>
    <span class="btn-outline">SUBSCRIBE</span>
  </div>
  <div class="socials"><span></span><span></span><span></span><span></span></div>
</section>

<footer class="section footer">
  <div class="footer-brand">BROVIK<small>BUILDERS</small></div>
  <div class="fcol" style="left:330px">
    <h5>USEFULL LINKS</h5>
    <ul>
      <li><span class="b"></span>Home</li>
      <li><span class="b"></span>About</li>
      <li><span class="b"></span>Services</li>
      <li><span class="b"></span>Works</li>
      <li><span class="b"></span>Contact</li>
    </ul>
  </div>
  <div class="fcol" style="left:580px">
    <h5>CONTACT US</h5>
    <ul>
      <li><svg width="16" height="20" viewBox="0 0 16 20"><path d="M8 0a8 8 0 0 0-8 8c0 6 8 12 8 12s8-6 8-12a8 8 0 0 0-8-8zm0 11a3 3 0 1 1 0-6 3 3 0 0 1 0 6z" fill="#fff"/></svg>214 Alder Row, Millbrook,<br>TX 75001</li>
      <li><svg width="16" height="16" viewBox="0 0 24 24"><path fill="#fff" d="M6.6 10.8a15.1 15.1 0 0 0 6.6 6.6l2.2-2.2c.3-.3.7-.4 1-.2 1.1.4 2.3.6 3.6.6.6 0 1 .4 1 1V20c0 .6-.4 1-1 1A17 17 0 0 1 3 4c0-.6.4-1 1-1h3.5c.6 0 1 .4 1 1 0 1.3.2 2.5.6 3.6.1.3 0 .7-.2 1z"/></svg>(855) 555-0142</li>
      <li><svg width="18" height="14" viewBox="0 0 18 14"><rect x="1" y="1" width="16" height="12" fill="none" stroke="#fff" stroke-width="2"/><path d="M1 1l8 7 8-7" fill="none" stroke="#fff" stroke-width="2"/></svg>info@brovikbuilders.com</li>
    </ul>
  </div>
  <div class="fcol" style="left:860px">
    <h5>FOLLOW US</h5>
    <div class="follow"><span></span><span></span><span style="width:60px"></span></div>
  </div>
</footer>

<div class="section copy">&copy; Brovik Builders - 2017 All rights reserved</div>

</body>
</html>
```